New Fresh design for online Rabbit Game

Hi,

we are a french company working on a online rabbits game for kids, and not kids.

Our website is www.zorvelo.fr, but you can look at the US version : www.quintamble.com

We buy our actual design 2 years ago, but we now think it's too boring and washed out...

We need yours talent to make a really more exacting, more colorful, fresh and dynamic design.

In our game, players have to breed and train rabbits and to make them run races. Players run again friends or players.

Players are kids, between 8 and 15 years. But best players are often parents of these kids !

Our ambiance is clearly funny. We really like if color theme or background look like a nice blue sky, and / or beach. Something that make people happy to come, and say "You are here on holly days to have fun !"

I think the best is if we have 2 layouts, one for the Home page, and one for all other page.

For home page, we are really open to any proposition, we just need to keep our features :
- registration (with rabbit preview)
- connection
- game preview (images slide with small text)
- live race preview (as we have actually)

For other pages layout, we need a layout with a standard container (maybe 850 px width?), and our 2 navigation's bar.

We only need psd, no html integration.

Thanks for your help, please ask me for any questions.
Updates

Hi, 

I have just added some information, concerning layout.

Also we have just committed the budget.

Target Market(s)

Mostly kids between 8 and 15 years.

Industry/Entity Type

It Company

Requirements
Must have
• We already have some characters, like Mr Wimble at the home page and our rabbits. We want to keep all of them, so new design have to match with there style (carton).

If you create an account, you will see we have a big nav bar with 6 tabs, and a little top bar. We absolutely need them to keep a easy navigation in website.

We also need some proposition of element style, like h1, h2, h3, hr, inputs, buttons, notification bubble, etc... So we can work to improve all our pages.
Nice to have
• I think the actual website is a little to wide (about 1000px width). Maybe something like 900px - 850px is more elegant ?
In this case, we can arrange pages to deal with it.

It can be cool if major colors are stil blue and green, to match a little with actual colors. But it's no very important.
Should not have
• We don't want too big header picture (for the all pages layout). I mean, players have to focus on the content.

We don't want photo realistic style, our style is cartoon.

We don't want flash. But Js animations are ok.

```html
<!DOCTYPE html>
<html lang="en">
<head>
<meta charset="utf-8">
<title>Quintamble – Racing and Breeding Game</title>
<link href="https://fonts.googleapis.com/css2?family=Signika:wght@400;600&family=PT+Sans:ital,wght@0,400;0,700;1,400&display=swap" rel="stylesheet">
<style>
  :root{
    --sky-top:#7fc4ea;
    --sky-bottom:#d6eef9;
    --hill:#7cbb3a;
    --hill-dark:#4f8f22;
    --soil:#5a3412;
    --soil-dark:#472709;
    --tab-dark:#66552a;
    --nav-yellow:#f7c600;
    --nav-yellow-light:#ffe14d;
    --nav-active:#5a4a16;
    --green:#7aa52a;
    --red:#d0312a;
    --text:#555;
    --panel-border:#d8e3e8;
    --panel-bg:#eaf6fa;
    --button-green:#6fae1f;
    --help-blue:#3a6fc0;
    --race-dark:#1e120a;
    --logo-orange:#f2a010;
  }
  *{box-sizing:border-box;margin:0;padding:0}
  html,body{width:1200px;height:864px;overflow:hidden}
  body{
    position:relative;
    font-family:"PT Sans",Arial,sans-serif;
    color:var(--text);
    background:linear-gradient(to bottom,var(--sky-top) 0,var(--sky-bottom) 700px);
  }
  .landscape{position:absolute;left:0;top:690px;width:1200px;height:100px}
  .soil{position:absolute;left:0;top:780px;width:1200px;height:84px;
    background:linear-gradient(to bottom,var(--soil),var(--soil-dark));}

  .top-bar{position:absolute;left:819px;top:0;width:192px;height:31px;
    background:var(--tab-dark);border-radius:0 0 8px 8px;
    display:flex;justify-content:center;align-items:center;gap:12px}
  .top-bar a{color:#fff;text-decoration:none;font-size:11px;font-weight:700}

  .brand-mascot{position:absolute;left:185px;top:14px;width:106px;height:80px;
    background:radial-gradient(ellipse at 50% 60%,#d9cdb8 0,#b8a78a 55%,transparent 70%)}
  .brand-name{position:absolute;left:300px;top:30px;font-family:"Signika",sans-serif;
    font-weight:600;font-size:40px;color:var(--logo-orange);letter-spacing:.5px}

  .page{position:absolute;left:185px;top:106px;width:826px;height:597px;
    background:#fafafa;border-radius:6px;box-shadow:0 2px 10px rgba(0,0,0,.18);overflow:hidden}
  .main-nav{height:45px;background:linear-gradient(to bottom,var(--nav-yellow-light),var(--nav-yellow));
    display:flex;align-items:center;padding-left:19px;gap:6px}
  .main-nav a{font-family:"Signika",sans-serif;font-size:14px;color:#4a3d10;text-decoration:none;
    padding:4px 14px;border-radius:3px;text-transform:uppercase}
  .main-nav a.active{background:var(--nav-active);color:#fff}

  .tagline{position:absolute;left:19px;top:60px;font-family:"Signika",sans-serif;font-size:14px;color:var(--green);text-transform:uppercase}
  .panel{position:absolute;background:linear-gradient(to bottom,#fff,var(--panel-bg));
    border:1px solid var(--panel-border);border-radius:4px}
  .panel-title{font-family:"Signika",sans-serif;font-size:17px;color:var(--green);text-transform:uppercase}
  .step{font-size:10px;font-weight:700;color:var(--red);text-transform:uppercase}
  .note{font-size:10px;font-weight:700;color:var(--green);text-transform:uppercase}
  .field{display:block;height:19px;background:#fff;border:1px solid #c9d3d8;border-radius:2px}
  .btn{display:inline-block;background:linear-gradient(to bottom,#8fcd3c,var(--button-green));
    color:#fff;font-size:10px;font-weight:700;text-align:center;border-radius:3px;border:1px solid #5a8f18}

  .register{left:17px;top:89px;width:383px;height:153px}
  .register .panel-title{position:absolute;left:16px;top:15px}
  .register .s1{position:absolute;left:16px;top:40px}
  .bunny-preview{position:absolute;left:16px;top:62px;width:60px;height:69px;
    background:radial-gradient(ellipse,#d5c9b4 0,#b4a488 55%,transparent 72%)}
  .options{position:absolute;left:108px;top:69px;list-style:none}
  .options li{display:flex;align-items:center;gap:8px;font-size:10px;font-weight:700;color:#777;height:17px}
  .options .arrow{width:9px;height:9px;border-radius:50%;background:var(--red);position:relative}
  .options .arrow::after{content:"";position:absolute;left:3px;top:2px;border:2.5px solid transparent}
  .options .prev::after{border-right:3px solid #fff;left:1px}
  .options .next::after{border-left:3px solid #fff;left:4px}
  .options .label{width:40px;text-align:center}
  .register .divider{position:absolute;left:191px;top:12px;width:1px;height:128px;background:#d9d9d9}
  .register .intro{position:absolute;left:203px;top:14px}
  .register .s2{position:absolute;left:203px;top:40px}
  .register .field{position:absolute;left:203px;top:56px;width:167px}
  .register .s3{position:absolute;left:203px;top:92px}
  .register .btn{position:absolute;left:203px;top:109px;width:48px;height:18px;line-height:16px}

  .login{left:417px;top:89px;width:391px;height:153px}
  .guide{position:absolute;left:12px;top:19px;width:99px;height:120px;
    background:radial-gradient(ellipse,#7aa84a 0,#4f7a30 50%,transparent 72%)}
  .login .panel-title{position:absolute;left:125px;top:15px}
  .login .lbl{position:absolute;top:40px;font-size:10px;font-weight:700;color:var(--red);text-transform:uppercase}
  .login .user-lbl{left:125px}.login .pass-lbl{left:245px}
  .login .user{position:absolute;left:125px;top:59px;width:110px}
  .login .pass{position:absolute;left:245px;top:59px;width:110px}
  .help{position:absolute;left:361px;top:60px;width:17px;height:17px;background:var(--help-blue);
    color:#fff;font-size:11px;font-weight:700;text-align:center;line-height:17px;border-radius:2px}
  .login .btn{position:absolute;left:125px;top:90px;width:50px;height:17px;line-height:15px}
  .forgot{position:absolute;left:183px;top:91px;font-size:10px;font-style:italic;color:#777}

  .rule{position:absolute;left:17px;top:267px;width:791px;height:1px;background:#e1e1e1}
  .section-title{position:absolute;top:282px;font-family:"Signika",sans-serif;font-size:13px;color:var(--green);text-transform:uppercase}
  .overview-title{left:19px}.races-title{left:417px}

  .overview{left:17px;top:305px;width:383px;height:261px;background:#fff}
  .tabs{position:absolute;left:35px;top:12px;display:flex;gap:4px;list-style:none}
  .tabs li{font-size:10px;color:#777;padding:3px 7px;text-transform:uppercase}
  .tabs li.active{background:#eef3f6;color:var(--help-blue);border:1px solid #dde5ea;border-bottom:none}
  .slide{position:absolute;left:10px;top:35px;width:363px;height:183px;
    background:linear-gradient(to bottom,#f4f4f4,#e8e8e8);border:1px solid #ddd}
  .caption{position:absolute;left:12px;top:226px;width:355px;font-size:10px;line-height:1.3;color:#777}

  .races{left:417px;top:305px;width:391px;height:261px;background:#fff}
  .race-view{position:absolute;left:9px;top:8px;width:374px;height:243px;
    background:linear-gradient(to bottom,#2b1a0e,var(--race-dark));border-radius:3px;overflow:hidden}
  .countdown{position:absolute;left:0;top:0;width:100%;height:100%;display:flex;align-items:center;justify-content:center;
    font-family:"PT Sans",Arial,sans-serif;font-size:190px;color:#fff;line-height:1}

  .partners{position:absolute;left:187px;top:803px;font-size:10px;color:#e7d6b8;text-transform:uppercase}
  .partner-badge{position:absolute;left:252px;top:799px;width:74px;height:24px;background:#3b78b8;border-radius:2px}
  .footer-links{position:absolute;left:687px;top:800px;font-size:9px;line-height:16px;color:#e7d6b8;text-transform:uppercase}
  .footer-links strong{color:#fff}
</style>
</head>
<body>
  <svg class="landscape" role="img" aria-label="Rolling green hills with daisies and a resting rabbit" viewBox="0 0 1200 100" preserveAspectRatio="none">
    <path d="M0 60 Q150 10 330 45 Q520 75 700 40 Q880 5 1050 35 Q1140 50 1200 30 L1200 100 L0 100 Z" fill="var(--hill)"/>
    <path d="M0 80 Q300 55 600 78 Q900 95 1200 70 L1200 100 L0 100 Z" fill="var(--hill-dark)"/>
  </svg>
  <div class="soil"></div>

  <nav class="top-bar">
    <a href="#">Home</a><a href="#">Mails</a><a href="#">Account</a><a href="#">Logout</a>
  </nav>

  <div class="brand-mascot" role="img" aria-label="Cartoon rabbit mascot"></div>
  <div class="brand-name">Quintamble</div>

  <main class="page">
    <nav class="main-nav">
      <a class="active" href="#">Home</a><a href="#">About us</a><a href="#">News</a><a href="#">Forum</a><a href="#">Records</a>
    </nav>

    <h1 class="tagline">The coolest racing and breeding game there is</h1>

    <section class="panel register">
      <h2 class="panel-title">New player</h2>
      <p class="step s1">1 - Choose your bunny</p>
      <div class="bunny-preview" role="img" aria-label="Preview of the chosen rabbit"></div>
      <ul class="options">
        <li><span class="arrow prev"></span><span class="label">Original</span><span class="arrow next"></span></li>
        <li><span class="arrow prev"></span><span class="label">Gray</span><span class="arrow next"></span></li>
        <li><span class="arrow prev"></span><span class="label">Male</span><span class="arrow next"></span></li>
      </ul>
      <div class="divider"></div>
      <p class="note intro">Register in just a couple of second!</p>
      <p class="step s2">2 - Choose a username</p>
      <span class="field"></span>
      <p class="step s3">3 - Ok! We're good to go!</p>
      <span class="btn">PLAY</span>
    </section>

    <section class="panel login">
      <div class="guide" role="img" aria-label="Mr Wimble, the turtle guide character"></div>
      <h2 class="panel-title">Connexion</h2>
      <span class="lbl user-lbl">Username</span>
      <span class="lbl pass-lbl">Password</span>
      <span class="field user"></span>
      <span class="field pass"></span>
      <span class="help">?</span>
      <span class="btn">PLAY</span>
      <span class="forgot">Forgotten your password?</span>
    </section>

    <div class="rule"></div>
    <h2 class="section-title overview-title">Game overview</h2>
    <h2 class="section-title races-title">Take part in races with other players</h2>

    <section class="panel overview">
      <ul class="tabs">
        <li>Your pen</li><li>Your allotment</li><li class="active">Professions</li><li>Universe</li>
      </ul>
      <div class="slide" role="img" aria-label="Cartoon alchemist and blacksmith characters showing the professions"></div>
      <p class="caption">Blacksmith, Alchemist, Gardner or Scientist! Progress in a profession and learn how to make really powerful objects!</p>
    </section>

    <section class="panel races">
      <div class="race-view" role="img" aria-label="Live race preview with rabbits on their lanes">
        <div class="countdown">1</div>
      </div>
    </section>
  </main>

  <span class="partners">Partners:</span>
  <span class="partner-badge"></span>
  <p class="footer-links">
    Rules · General terms and conditions · Contact · <strong>Quintamble.com 3.0</strong><br>
    Copyright © 2012 Quintamble | Designed by <strong>Corvane Studio.</strong>
  </p>
</body>
</html>
```